Modern design company business card design

We are a design oriented construction firm. The owner is an architect and licensed General Contractor and accomplished furniture designer. We do new home construction and large scale remodeling and office design. We would like a design for our new business cards that is clean and modern, but relatable. We like the bright green color of our logo mixed with different shades of grey. We're also open to reinterpreting the logo.

Target Market(s)

Potential design clients,
Construction clients

Industry/Entity Type

Architecture

Contact Information for Business Card

Tall Maple Design | Build Inc. (optional with logo, Inc. optional)Jeffrey MorganOwner (optional)317.555.0148 cell317.431.8056 officejmorgan@greensquareinc.comwww.greensquareinc.com

Font styles to use
Sans Serif
Other font styles liked:
• Avenir

Requirements
Nice to have
• I like designs that have some continuity between the front and back, i.e. similar layouts or graphic elements that wrap around the card. I tend to prefer horizontal over vertical, but that's not a have to. I also tend to prefer white or recycled paper.

```html
<!DOCTYPE html>
<html lang="en">
<head>
<meta charset="utf-8">
<title>Tall Maple Design | Build – Business Card</title>
<link href="https://fonts.googleapis.com/css2?family=Mulish:wght@400;600;700&display=swap" rel="stylesheet">
<style>
  :root {
    --backdrop: #000000;
    --paper: #ffffff;
    --brand-green: #9fce55;
    --ink: #111111;
    --grey: #8a8a8a;
  }
  * { margin: 0; padding: 0; box-sizing: border-box; }
  html, body {
    width: 1200px; height: 900px; overflow: hidden;
    background: var(--backdrop);
    font-family: "Mulish", "Avenir", sans-serif;
  }
  .stage { position: relative; width: 1200px; height: 900px; }

  .card {
    position: absolute; top: 275px; width: 477px; height: 294px;
    background: var(--paper);
  }
  .card--front { left: 116px; border-radius: 0 52px 0 62px; }
  .card--back  { left: 622px; border-radius: 52px 0 62px 0; }

  .brand { position: absolute; display: flex; align-items: center; }
  .brand__dot {
    width: 12px; height: 12px; border-radius: 50%;
    background: var(--brand-green); margin-right: 12px; flex: none;
  }
  .brand__name {
    color: var(--grey); font-weight: 400; line-height: 1.25;
    font-size: 15px; letter-spacing: 1.2px; text-align: left;
  }
  .brand__name span { display: block; }

  .card--front .brand { right: 174px; top: 132px; }
  .card--back .brand  { right: 111px; top: 152px; }

  .person { position: absolute; right: 28px; top: 37px; text-align: right; }
  .person__name { font-size: 16.5px; font-weight: 700; color: var(--brand-green); line-height: 1.1; }
  .person__role { font-size: 12.5px; font-weight: 600; color: var(--ink); line-height: 1.2; }

  .contacts { position: absolute; right: 26px; top: 186px; list-style: none; }
  .contacts li {
    display: flex; justify-content: flex-end; align-items: center;
    height: 20px; font-size: 12.5px; color: var(--ink); font-weight: 600;
  }
  .contacts svg { width: 11px; height: 11px; margin-left: 6px; fill: none; stroke: var(--brand-green); stroke-width: 2; }
  .contacts .icon-fill { fill: var(--brand-green); stroke: none; }
</style>
</head>
<body>
<main class="stage">
  <section class="card card--front" aria-label="Card front">
    <div class="person">
      <p class="person__name">Dennis Holloway</p>
      <p class="person__role">Owner</p>
    </div>
    <div class="brand">
      <div class="brand__dot"></div>
      <p class="brand__name"><span>Tall Maple</span><span>Design | Build Inc.</span></p>
    </div>
    <ul class="contacts">
      <li>317.555.0172
        <svg viewBox="0 0 12 12"><path class="icon-fill" d="M2.5 1l2 2.2-1 1.3c.8 1.6 2 2.8 3.6 3.6l1.3-1 2.2 2-1 1.6C5.5 10.5 1.5 6.5.9 2z"/></svg></li>
      <li>317.555.0148
        <svg viewBox="0 0 12 12"><rect x="3" y="1" width="6" height="10" rx="1"/></svg></li>
      <li>dholloway@tallmapleinc.example
        <svg viewBox="0 0 12 12"><rect class="icon-fill" x="1" y="2.5" width="10" height="7"/><path d="M1.5 3l4.5 3.5L10.5 3" stroke="#fff" stroke-width="1"/></svg></li>
      <li>www.tallmapleinc.example
        <svg viewBox="0 0 12 12"><path d="M5 7l2-2M4 5.5L2.5 7a1.8 1.8 0 002.5 2.5L6.5 8M8 6.5L9.5 5A1.8 1.8 0 007 2.5L5.5 4" stroke-width="1.4"/></svg></li>
    </ul>
  </section>

  <section class="card card--back" aria-label="Card back">
    <div class="brand">
      <div class="brand__dot"></div>
      <p class="brand__name"><span>Tall Maple</span><span>Design | Build Inc.</span></p>
    </div>
  </section>
</main>
</body>
</html>
```